Banner signature

Hi, looking for a banner for email signature 728 px wide and 200 px high
Could we have our 10 year logo and premium logo, a similar look and feel of our previous banner design (I've attached) and also include an aboriginal design with the Wording
This email comes to you from Gubbi Gubbi country
I've attached an example of some look and feels that we like.
Can we have the background of banner the Blue colour of our Fern & Pebble logo and

```html
<!DOCTYPE html>
<html lang="en">
<head>
<meta charset="utf-8">
<title>Email Signature Banner</title>
<link rel="stylesheet" href="https://fonts.googleapis.com/css2?family=Caveat+Brush&family=Kalam:wght@700&family=Permanent+Marker&display=swap">
<style>
  :root {
    --stage: #1d1d1d;
    --brand-blue: #0a63b4;
    --brand-blue-deep: #0550a0;
    --sky: #1aa3ea;
    --sky-mid: #3bb3ef;
    --sky-light: #cfe4f2;
    --paper: #f4f7fb;
    --white: #ffffff;
    --gold: #d9b343;
    --gold-light: #f6e08a;
    --gold-deep: #a9801f;
  }
  html, body {
    margin: 0;
    width: 1200px;
    height: 710px;
    overflow: hidden;
    background: var(--stage);
  }
  .banner {
    position: absolute;
    left: 50px;
    top: 228px;
    width: 1100px;
    height: 254px;
    overflow: hidden;
    background: var(--paper);
  }
  .banner-backdrop { position: absolute; inset: 0; }
  .brand-mark {
    position: absolute;
    left: 14px;
    top: 12px;
    width: 62px;
    height: 62px;
    border-radius: 50%;
    background: var(--gold);
  }
  .intro-line {
    position: absolute;
    left: 110px;
    top: 20px;
    width: 440px;
    margin: 0;
    text-align: center;
    font-family: "Kalam", "Caveat Brush", sans-serif;
    font-weight: 700;
    font-size: 29px;
    line-height: 1.2;
    color: var(--white);
  }
  .nation-name {
    position: absolute;
    left: 50px;
    top: 50px;
    width: 550px;
    margin: 0;
    text-align: center;
    font-family: "Permanent Marker", "Caveat Brush", cursive;
    font-weight: 400;
    font-size: 78px;
    line-height: 1.15;
    word-spacing: 16px;
    color: var(--white);
  }
  .country-word {
    position: absolute;
    left: 200px;
    top: 170px;
    margin: 0;
    font-family: "Permanent Marker", "Caveat Brush", cursive;
    font-size: 60px;
    line-height: 1.15;
    color: var(--sky);
  }
  .anniversary-badge {
    position: absolute;
    left: 705px;
    top: -8px;
    width: 262px;
    height: 262px;
    border-radius: 50%;
    background: radial-gradient(circle at 40% 35%, var(--gold-light), var(--gold) 55%, var(--gold-deep));
  }
</style>
</head>
<body>
  <section class="banner">
    <svg class="banner-backdrop" width="1100" height="254" viewBox="0 0 1100 254">
      <defs>
        <linearGradient id="bandFill" x1="0" y1="0" x2="1" y2="0">
          <stop offset="0" stop-color="var(--brand-blue-deep)"/>
          <stop offset="0.55" stop-color="var(--sky)"/>
          <stop offset="1" stop-color="var(--sky)"/>
        </linearGradient>
      </defs>
      <rect width="1100" height="254" fill="url(#bandFill)"/>
      <path class="lower-wave" d="M0 176 H540 C600 176 625 150 650 110 L690 254 H0 Z" fill="var(--paper)"/>
      <g role="img" aria-label="Aboriginal circle artwork of radiating blue and white strokes">
        <circle cx="836" cy="124" r="248" fill="var(--sky-mid)"/>
        <circle cx="836" cy="124" r="158" fill="var(--white)"/>
      </g>
      <g role="img" aria-label="Faint aboriginal concentric circle motif">
        <circle cx="95" cy="254" r="88" fill="var(--sky-light)" opacity="0.7"/>
      </g>
    </svg>

    <div class="brand-mark" aria-hidden="true"></div>

    <p class="intro-line">This email comes to you from</p>
    <h1 class="nation-name">Gubbi Gubbi</h1>
    <p class="country-word">Country</p>

    <div class="anniversary-badge" role="img" aria-label="10 year anniversary badge"></div>
  </section>
</body>
</html>
```